Music Quizz Application

Hello,

I want a new design for my Blind test (music quizz) application on Korvex. You will find attached the images I want to replace. I need something with the same element (menu / song title) but with a different look!

Same, new icon, you have carte blanche to this one.

I am looking for something fresh…. I'm looking for something with a real artistic choice, contrast, colours, etc.

As a marketing screenshot, I want something classic, you'll find an example attached, feel free to innovate.

To sum-up :

- One new view for my App
- One new icon
- One marketing screenshot

screen resolution :
640×960
icon resolution :
1024x1024

Target Market(s)

15-30 years

Industry/Entity Type

Marketing

```html
<!DOCTYPE html>
<html lang="en">
<head>
<meta charset="utf-8">
<title>Music Quizz</title>
<link href="https://fonts.googleapis.com/css2?family=Arimo:wght@400;700&display=swap" rel="stylesheet">
<style>
  :root {
    --status-bg: #4f575b;
    --status-text: #ffffff;
    --ink: #1f3b4a;
    --header-a: #7fd6d8;
    --header-b: #a9e6dd;
    --header-c: #6fc9c9;
    --tab-active: #6fcfd0;
    --tab-mid: #cfd8cc;
    --tab-right: #a3dcc4;
    --tab-border: #26434e;
    --page-bg: #9fd8c0;
    --row-bg: #cfd8cd;
    --scroll-track: #6a8f80;
    --scroll-thumb: #dfe6e2;
    --icon: #111111;
  }
  * { box-sizing: border-box; margin: 0; padding: 0; }
  html, body { width: 800px; height: 1200px; overflow: hidden; background: var(--page-bg); }
  body { font-family: "Arimo", Arial, sans-serif; color: var(--ink); }
  .screen { position: relative; width: 800px; height: 1200px; background: var(--page-bg); overflow: hidden; }

  .status-bar { position: absolute; left: 0; top: 0; width: 800px; height: 50px; background: var(--status-bg); color: var(--status-text); font-weight: 700; font-size: 27px; }
  .status-bar .carrier { position: absolute; left: 10px; top: 10px; display: flex; align-items: flex-end; gap: 8px; }
  .status-bar .time { position: absolute; left: 0; right: 0; top: 10px; text-align: center; }
  .status-bar .battery { position: absolute; right: 14px; top: 13px; }

  .app-header { position: absolute; left: 0; top: 50px; width: 800px; height: 110px; }
  .header-texture { position: absolute; inset: 0; background: linear-gradient(90deg, var(--header-c), var(--header-b) 35%, var(--header-a) 60%, var(--header-b) 85%, var(--header-c)); }
  .app-title { position: absolute; left: 0; right: 0; top: 20px; text-align: center; font-weight: 700; font-size: 62px; color: var(--ink); text-shadow: 2px 3px 4px rgba(0,0,0,0.35); }
  .header-btn { position: absolute; top: 14px; width: 70px; height: 80px; }
  .header-btn.menu { left: 10px; }
  .header-btn.settings { right: 10px; }

  .tabs { position: absolute; left: 0; top: 160px; width: 800px; height: 111px; display: flex; border-top: 2px solid var(--tab-border); }
  .tab { flex: 1; display: flex; align-items: center; justify-content: center; font-weight: 700; font-size: 28px; color: var(--ink); border-left: 2px solid var(--tab-border); }
  .tab:first-child { border-left: none; background: var(--tab-active); }
  .tab.rankings { background: var(--tab-mid); }
  .tab.community { background: var(--tab-right); }

  .menu-list { position: absolute; left: 12px; top: 325px; width: 772px; list-style: none; }
  .menu-item { position: relative; height: 140px; margin-bottom: 13px; background: var(--row-bg); display: flex; align-items: center; }
  .menu-item .icon { position: absolute; left: 45px; width: 160px; height: 100px; display: flex; align-items: center; justify-content: center; }
  .menu-item .label { position: absolute; left: 273px; font-size: 37px; letter-spacing: 0.5px; }
  .battles-amp { font-size: 34px; margin: 0 14px; color: var(--ink); }

  .scrollbar { position: absolute; left: 788px; top: 271px; width: 12px; height: 929px; background: var(--scroll-track); }
  .scrollbar .thumb { position: absolute; left: 0; top: 327px; width: 12px; height: 202px; background: var(--scroll-thumb); }
</style>
</head>
<body>
<div class="screen">

  <div class="status-bar">
    <div class="carrier">
      <svg width="50" height="24" viewBox="0 0 50 24" aria-hidden="true">
        <rect x="0" y="18" width="6" height="6" fill="#fff"/>
        <rect x="10" y="14" width="6" height="10" fill="#fff"/>
        <rect x="20" y="10" width="6" height="14" fill="#fff"/>
        <rect x="30" y="5" width="6" height="19" fill="#fff"/>
        <rect x="40" y="0" width="6" height="24" fill="#fff"/>
      </svg>
      <span>VELNET</span>
    </div>
    <div class="time">2:34</div>
    <svg class="battery" width="52" height="26" viewBox="0 0 52 26" aria-hidden="true">
      <rect x="1" y="1" width="45" height="24" rx="3" fill="none" stroke="#fff" stroke-width="2"/>
      <rect x="5" y="5" width="37" height="16" fill="#fff"/>
      <rect x="47" y="8" width="4" height="10" fill="#fff"/>
    </svg>
  </div>

  <header class="app-header">
    <div class="header-texture" role="img" aria-label="Soft teal mosaic of blurred squares behind the title"></div>
    <svg class="header-btn menu" viewBox="0 0 70 80" aria-label="Menu">
      <polygon points="35,4 66,22 66,58 35,76 4,58 4,22" fill="none" stroke="#1f3b4a" stroke-width="5"/>
      <g fill="#1f3b4a">
        <circle cx="23" cy="28" r="4"/><rect x="30" y="25" width="19" height="6" rx="2"/>
        <circle cx="23" cy="40" r="4"/><rect x="30" y="37" width="19" height="6" rx="2"/>
        <circle cx="23" cy="52" r="4"/><rect x="30" y="49" width="19" height="6" rx="2"/>
      </g>
    </svg>
    <h1 class="app-title">Music Quizz</h1>
    <svg class="header-btn settings" viewBox="0 0 70 80" aria-label="Settings">
      <polygon points="35,4 66,22 66,58 35,76 4,58 4,22" fill="none" stroke="#1f3b4a" stroke-width="5"/>
      <g fill="#1f3b4a" transform="translate(35 40)">
        <circle r="9"/>
        <rect x="-3" y="-13" width="6" height="26"/>
        <rect x="-3" y="-13" width="6" height="26" transform="rotate(45)"/>
        <rect x="-3" y="-13" width="6" height="26" transform="rotate(90)"/>
        <rect x="-3" y="-13" width="6" height="26" transform="rotate(135)"/>
        <circle r="3.5" fill="#8fdcd8"/>
      </g>
    </svg>
  </header>

  <nav class="tabs">
    <div class="tab home">HOME</div>
    <div class="tab rankings">RANKINGS</div>
    <div class="tab community">COMMUNITY</div>
  </nav>

  <ul class="menu-list">
    <li class="menu-item">
      <span class="icon">
        <svg width="90" height="70" viewBox="0 0 90 70" aria-hidden="true">
          <g fill="#111">
            <rect x="22" y="8" width="5" height="46"/>
            <rect x="50" y="2" width="5" height="46"/>
            <polygon points="22,8 55,2 55,12 22,18"/>
            <ellipse cx="17" cy="55" rx="10" ry="8"/>
            <ellipse cx="45" cy="49" rx="10" ry="8"/>
            <polygon points="58,58 80,32 87,38 65,63 56,66"/>
          </g>
        </svg>
      </span>
      <span class="label">SONG REQUESTS</span>
    </li>
    <li class="menu-item">
      <span class="icon">
        <svg width="64" height="60" viewBox="0 0 64 60" aria-hidden="true">
          <path d="M38 10 L52 2" stroke="#111" stroke-width="3"/>
          <path d="M12 20 H52 Q62 20 62 40 Q62 56 52 52 L44 44 H20 L12 52 Q2 56 2 40 Q2 20 12 20 Z" fill="#111"/>
          <rect x="13" y="30" width="12" height="4" fill="#cfd8cd"/><rect x="17" y="26" width="4" height="12" fill="#cfd8cd"/>
          <circle cx="47" cy="28" r="2.5" fill="#cfd8cd"/><circle cx="47" cy="37" r="2.5" fill="#cfd8cd"/>
          <circle cx="42.5" cy="32.5" r="2.5" fill="#cfd8cd"/><circle cx="51.5" cy="32.5" r="2.5" fill="#cfd8cd"/>
        </svg>
        <span class="battles-amp">&amp;</span>
        <svg width="64" height="60" viewBox="0 0 64 60" aria-hidden="true">
          <path d="M38 10 L52 2" stroke="#111" stroke-width="3"/>
          <path d="M12 20 H52 Q62 20 62 40 Q62 56 52 52 L44 44 H20 L12 52 Q2 56 2 40 Q2 20 12 20 Z" fill="#111"/>
          <rect x="13" y="30" width="12" height="4" fill="#cfd8cd"/><rect x="17" y="26" width="4" height="12" fill="#cfd8cd"/>
          <circle cx="47" cy="28" r="2.5" fill="#cfd8cd"/><circle cx="47" cy="37" r="2.5" fill="#cfd8cd"/>
          <circle cx="42.5" cy="32.5" r="2.5" fill="#cfd8cd"/><circle cx="51.5" cy="32.5" r="2.5" fill="#cfd8cd"/>
        </svg>
      </span>
      <span class="label">BATTLES</span>
    </li>
    <li class="menu-item">
      <span class="icon">
        <svg width="68" height="60" viewBox="0 0 68 60" aria-hidden="true">
          <path d="M6 2 H62 Q66 2 66 6 V38 Q66 42 62 42 H40 L34 54 L28 42 H6 Q2 42 2 38 V6 Q2 2 6 2 Z" fill="#111"/>
        </svg>
      </span>
      <span class="label">FORUMS</span>
    </li>
    <li class="menu-item">
      <span class="icon">
        <svg width="68" height="60" viewBox="0 0 68 60" aria-hidden="true">
          <g fill="#111">
            <circle cx="26" cy="16" r="13"/>
            <path d="M2 58 Q2 34 26 32 Q50 34 50 58 Z"/>
            <ellipse cx="50" cy="24" rx="16" ry="12"/>
          </g>
        </svg>
      </span>
      <span class="label">MEMBERS</span>
    </li>
    <li class="menu-item">
      <span class="icon">
        <svg width="68" height="64" viewBox="0 0 68 64" aria-hidden="true">
          <g fill="#111">
            <circle cx="34" cy="9" r="8"/>
            <circle cx="16" cy="18" r="8"/>
            <circle cx="52" cy="18" r="8"/>
            <path d="M2 50 Q2 26 16 27 Q26 27 28 36 L34 30 L40 36 Q42 27 52 27 Q66 26 66 50 Q60 46 56 56 Q46 46 40 60 L34 52 L28 60 Q22 46 12 56 Q8 46 2 50 Z"/>
            <path d="M24 38 Q24 18 34 18 Q44 18 44 38 Z"/>
          </g>
        </svg>
      </span>
      <span class="label">TEAMS</span>
    </li>
  </ul>

  <div class="scrollbar"><div class="thumb"></div></div>
</div>
</body>
</html>
```